Logo and Card design for KRV Home Solutions LLC

I need an edgier logo and business card designs. Current logo attached. I like the colors below. I would like the logo to incorporate a home in the design.
Title = Principal-Acquisitions
Email:KRVHOMESOLUTIONS@fernmail.example
555-214-0937
facebook
IG
2 sided business card with the front being contact info a slogan about selling a home fast. The back incorporating What we do. Buy houses, land, or commercial property as is. We find solutions to make the process of selling simple and fair.

Target Market(s)

Motivated house sellers.

Industry/Entity Type

Business

Contact Information for Business Card

Who we are: We are a Faith based Real Estate Investment Company. We pay cash for homes in any condition and can close quick. Whatever the reason you need to sell fast, we can help. We believe in creating win-win solutions to help you in your time of need. We care! We can help!

Logo Text

KRV Home Solutions LLC

Font styles to use
Sans Serif

Colors
33a6d7
0355a3
85abd2
cee9f5
9d9d9d
b2b2b2
ffffff

Requirements
Must have
• Old logo attached. I want something edgier.
• Company name, phone number, description on the back of what we can do. Pay all cash. Buy in as is condition. No fees,Commisions or closing costs.Close quick. No hassles with solutions to meet your unique situation.
• Call today for an offer within 24 hours.

```html
<!DOCTYPE html>
<html lang="en">
<head>
<meta charset="utf-8">
<title>KRV Home Solutions – Business Card</title>
<link href="https://fonts.googleapis.com/css2?family=Work+Sans:wght@400;500;600;700&display=swap" rel="stylesheet">
<style>
  :root {
    --stage: #2a2727;
    --navy: #233d80;
    --navy-deep: #1b3170;
    --ink-blue: #1f3a7c;
    --grey: #5f5f63;
    --grey-light: #9d9d9d;
    --white: #ffffff;
    --text: #444448;
  }
  html, body {
    margin: 0;
    padding: 0;
    width: 1200px;
    height: 1050px;
    overflow: hidden;
    background: var(--stage);
    font-family: "Work Sans", Arial, sans-serif;
  }
  .canvas {
    position: relative;
    width: 1200px;
    height: 1050px;
  }
  .card {
    position: absolute;
    left: 250px;
    width: 700px;
    height: 400px;
    box-sizing: border-box;
    overflow: hidden;
    box-shadow: 0 10px 30px rgba(0,0,0,.5);
  }

  /* Back side */
  .card-back {
    top: 95px;
    background: linear-gradient(135deg, var(--navy) 0%, var(--navy-deep) 100%);
    color: var(--white);
    text-align: center;
  }
  .brand {
    display: flex;
    align-items: center;
    justify-content: center;
    gap: 12px;
    font-weight: 700;
    letter-spacing: .02em;
  }
  .brand-mark {
    width: 22px;
    height: 22px;
  }
  .card-back .brand {
    margin-top: 105px;
    font-size: 34px;
    color: var(--white);
  }
  .card-back .brand-mark { background: var(--white); }
  .what-we-do {
    margin: 70px auto 0;
    width: 560px;
    font-size: 17px;
    line-height: 1.35;
    font-weight: 400;
  }
  .what-we-do p { margin: 0; }

  /* Front side */
  .card-front {
    top: 555px;
    background: var(--white);
  }
  .card-front .brand {
    position: absolute;
    top: 48px;
    right: 40px;
    font-size: 22px;
    color: var(--ink-blue);
  }
  .card-front .brand-mark { background: var(--ink-blue); width: 18px; height: 18px; }
  .swoosh {
    position: absolute;
    inset: 0;
  }
  .identity {
    position: absolute;
    left: 44px;
    top: 150px;
  }
  .company-name {
    margin: 0;
    font-size: 26px;
    font-weight: 500;
    color: var(--ink-blue);
    letter-spacing: .01em;
  }
  .job-title {
    margin: 2px 0 0;
    font-size: 15px;
    color: var(--text);
  }
  .contact-list {
    list-style: none;
    margin: 26px 0 0;
    padding: 0;
    font-size: 15px;
    color: var(--text);
    line-height: 1.45;
  }
  .contact-list li {
    display: flex;
    align-items: center;
    gap: 10px;
  }
  .contact-icon {
    width: 13px;
    height: 13px;
    flex: none;
  }
  .dot {
    width: 11px;
    height: 11px;
    border-radius: 50%;
    background: var(--ink-blue);
    margin: 0 1px;
    flex: none;
  }
  .slogan {
    position: absolute;
    right: 44px;
    top: 198px;
    margin: 0;
    font-size: 14px;
    font-weight: 500;
    letter-spacing: .2em;
    color: #333;
  }
</style>
</head>
<body>
<div class="canvas">

  <section class="card card-back" aria-label="Business card back">
    <div class="brand"><span class="brand-mark"></span>KRV HOME SOLUTIONS</div>
    <div class="what-we-do">
      <p>Pay all cash. Buy in as is condition. No fees,Commisions</p>
      <p>or closing costs.Close quick. No hassles with solutions</p>
      <p>to meet your unique situation.</p>
      <p>Call today for an offer within 24 hours.</p>
    </div>
  </section>

  <section class="card card-front" aria-label="Business card front">
    <svg class="swoosh" width="700" height="400" viewBox="0 0 700 400" aria-hidden="true">
      <path d="M700 250 C590 262 470 300 395 400 L700 400 Z" fill="var(--grey)"/>
      <path d="M700 262 C600 275 490 310 420 400 L700 400 Z" fill="var(--white)"/>
      <path d="M700 268 C610 282 505 318 435 400 L700 400 Z" fill="var(--navy)"/>
    </svg>

    <div class="brand"><span class="brand-mark"></span>KRV HOME SOLUTIONS</div>

    <div class="identity">
      <h1 class="company-name">KRV HOME SOLUTIONS</h1>
      <p class="job-title">Principal-Acquisitions</p>
      <ul class="contact-list">
        <li>
          <svg class="contact-icon" viewBox="0 0 24 24" aria-hidden="true">
            <circle cx="12" cy="12" r="12" fill="var(--ink-blue)"/>
            <path d="M8 6.5l2 0 1 3-1.3 1.2a7 7 0 0 0 3.6 3.6L14.5 13l3 1v2a1.5 1.5 0 0 1-1.6 1.5A10 10 0 0 1 6.5 8.1 1.5 1.5 0 0 1 8 6.5z" fill="var(--white)"/>
          </svg>
          555-214-0937
        </li>
        <li><span class="dot"></span>/krvhomesolutions</li>
        <li><span class="dot"></span>@krvhomesolutions</li>
        <li>
          <svg class="contact-icon" viewBox="0 0 24 24" aria-hidden="true">
            <circle cx="12" cy="12" r="12" fill="var(--ink-blue)"/>
            <rect x="6" y="8" width="12" height="8" fill="none" stroke="var(--white)" stroke-width="1.5"/>
            <path d="M6 8l6 5 6-5" fill="none" stroke="var(--white)" stroke-width="1.5"/>
          </svg>
          krvhomesolutions@fernmail.example
        </li>
      </ul>
    </div>

    <p class="slogan">SELLING A HOME FAST</p>
  </section>

</div>
</body>
</html>
```